Corvana Tongue Works, LLC

We need a business card that includes information about our business and conveys a reliable business that provides document translation services and interpreters for a variety of corporate and individual clients. We want to come across as professional, reliable, yet approachable. It should include the following on one side:

ESL / ENL Language Classes, Private Lessons, and Online Tutors
PLEXA Training and Testing
Translating & Interpreting Services
Contact us about Over-the-Phone Interpreting in over 200 languages
24/7/365
www.corvanatongue.example

The other side should include (555) 481-3062

Rhoda Pelling, President
482 Garnet Ave., Ste. 219
Indianapolis, IN 40917

Please add USA as part of the address. Also, please add rmpelling@corvanatongueworks.example as the e-mail address. Thank you.

Target Market(s)

Business professionals, their families, the international community

Industry/Entity Type

Business

Contact Information for Business Card

24/7/365
www.corvanatongue.example

(555) 481-3062

Rhoda Pelling, President
482 Garnet Ave., Ste. 219
Indianapolis, IN 40917
USA

Font styles to use
Sans Serif

Colors

Designer to choose colors to be used in the design.

Requirements
Must have
• See project description
• e-mail address and web address
• Phone number
Nice to have
• a globe
• physical address
Should not have
• Should not have the same color scheme as other agencies in our market in Indiana unless it is blue and black. No purple or yellow.

```html
<!DOCTYPE html>
<html lang="en">
<head>
<meta charset="utf-8">
<title>Corvana Tongue Works, LLC — Business Card</title>
<link href="https://fonts.googleapis.com/css2?family=Work+Sans:wght@400;500;600&family=Roboto:wght@400;500&display=swap" rel="stylesheet">
<style>
  :root {
    --bg: #4a433d;
    --ink: #111111;
    --card-black: #0b0b0b;
    --paper: #ffffff;
    --blue: #2a98d8;
    --blue-light: #5fb7e8;
    --white: #ffffff;
  }
  * { margin: 0; padding: 0; box-sizing: border-box; }
  html, body { width: 1200px; height: 930px; overflow: hidden; }
  body {
    background: var(--bg);
    font-family: "Work Sans", sans-serif;
    position: relative;
  }
  .card {
    position: absolute;
    width: 640px;
    height: 366px;
    border-radius: 16px;
    overflow: hidden;
    box-shadow: 0 10px 24px rgba(0,0,0,.35);
  }

  /* Back side */
  .card-back {
    left: 60px; top: 60px;
    background: var(--card-black);
    color: var(--white);
    text-align: center;
  }
  .brand {
    display: flex;
    align-items: center;
    gap: 16px;
  }
  .brand-mark {
    width: 76px; height: 76px;
    border-radius: 50%;
    flex-shrink: 0;
  }
  .brand-name {
    font-family: "Work Sans", sans-serif;
    font-weight: 500;
    font-size: 30px;
    line-height: 1.05;
    text-align: left;
  }
  .card-back .brand { justify-content: center; margin-top: 44px; }
  .card-back .brand-mark { background: var(--white); }
  .card-back .brand-name { color: var(--blue); }
  .services {
    margin-top: 28px;
    font-family: "Roboto", sans-serif;
    font-size: 16px;
    line-height: 1.4;
  }
  .divider-back {
    width: 530px; height: 2px;
    background: var(--blue);
    margin: 16px auto 12px;
  }
  .contact-note {
    font-family: "Roboto", sans-serif;
    font-size: 16px;
    line-height: 1.4;
  }

  /* Front side */
  .card-front {
    left: 500px; top: 500px;
    background: var(--paper);
    color: var(--ink);
  }
  .card-front .brand { position: absolute; right: 40px; top: 26px; }
  .card-front .brand-mark { background: var(--blue); width: 70px; height: 70px; }
  .card-front .brand-name { color: var(--ink); font-size: 26px; }
  .person {
    position: absolute;
    left: 0; top: 118px;
    padding-left: 44px;
  }
  .person::before, .person::after {
    content: "";
    position: absolute;
    top: 6px; height: 50px;
  }
  .person::before { left: 0; width: 28px; background: var(--blue); }
  .person::after { left: 32px; width: 5px; background: var(--ink); }
  .person-name {
    font-size: 32px;
    font-weight: 500;
    line-height: 40px;
    color: var(--blue);
    letter-spacing: .5px;
    text-transform: uppercase;
  }
  .person-title { font-size: 17px; line-height: 22px; }
  .rule-front {
    position: absolute;
    left: 132px; right: 40px; top: 164px;
    height: 1.5px;
    background: var(--blue);
  }
  .contact-list {
    position: absolute;
    left: 50px; top: 214px;
    list-style: none;
    font-size: 17px;
    line-height: 1.35;
  }
  .contact-list li { display: flex; align-items: center; gap: 10px; }
  .contact-list svg { width: 13px; height: 13px; fill: none; stroke: var(--blue); stroke-width: 2; }
  .address {
    position: absolute;
    right: 40px; top: 180px;
    font-size: 16px;
    line-height: 1.35;
    text-align: right;
  }
  .swoosh { position: absolute; left: 0; bottom: 0; width: 640px; height: 120px; }
</style>
</head>
<body>

  <section class="card card-back" aria-label="Card back">
    <div class="brand">
      <span class="brand-mark"></span>
      <span class="brand-name">Corvana<br>Tongue<br>Works LLC</span>
    </div>
    <p class="services">
      ESL / ENL Language Classes, Private Lessons, and Online Tutors<br>
      PLEXA Training and Testing<br>
      Translating &amp; Interpreting Services
    </p>
    <div class="divider-back"></div>
    <p class="contact-note">
      Contact us about Over-the-Phone Interpreting in over 200 languages<br>
      24/7/365
    </p>
  </section>

  <section class="card card-front" aria-label="Card front">
    <div class="brand">
      <span class="brand-mark"></span>
      <span class="brand-name">Corvana<br>Tongue<br>Works LLC</span>
    </div>

    <div class="person">
      <h1 class="person-name">Rhoda Pelling</h1>
      <p class="person-title">President</p>
    </div>
    <div class="rule-front"></div>

    <ul class="contact-list">
      <li><svg viewBox="0 0 14 14"><path d="M3 1l2 3-1.5 1.5a8 8 0 0 0 5 5L10 9l3 2-1 2C6 13 1 8 1 2z"/></svg>(555) 481-3062</li>
      <li><svg viewBox="0 0 14 14"><rect x="1" y="3" width="12" height="8"/><path d="M1 3l6 5 6-5"/></svg>rmpelling@corvanatongueworks.example</li>
      <li><svg viewBox="0 0 14 14"><circle cx="7" cy="7" r="6"/><path d="M1 7h12M7 1c-3 3-3 9 0 12M7 1c3 3 3 9 0 12"/></svg>www.corvanatongue.example</li>
    </ul>

    <p class="address">482 Garnet Ave., Ste. 219<br>Indianapolis, IN 40917 USA</p>

    <svg class="swoosh" viewBox="0 0 640 120" preserveAspectRatio="none" aria-hidden="true">
      <path d="M0 98 C220 110 460 80 640 16 L640 120 L0 120 Z" fill="var(--blue)"/>
      <path d="M0 90 C220 104 460 74 640 8 L640 20 C460 86 220 112 0 102 Z" fill="var(--ink)"/>
      <path d="M0 104 C240 114 470 84 640 28 L640 42 C470 96 240 120 0 112 Z" fill="var(--blue-light)" opacity=".6"/>
    </svg>
  </section>

</body>
</html>
```